'Little Lantern' promotional brochure

We have designed a 6 week program to educate impending first-time parents about the things they need to know to survive the first 6 months. Sessions delivered by general practitioner/family doctor, dietician, physiotherapist, speech pathologist and psychologist. Our promotional blurb is: 'A comprehensive education program for first-time parents-to-be, delivered over 6 weeks by health professionals in your community, about everything you need to know to look after your baby (and yourself!) in the first 6 months'. I now want to put together a promotional brochure to be distributed to those couples who express an interest which will provide further details of what will be delivered in the course.
Updates
In terms of layout, I envisaged a double sided A4 size, foldable into 3 sections, but very happy to be guided on this.
Target Market(s)
To appeal to a young, well educated demographic. First time parents couples.
Industry/Entity Type
Medical
Font styles to use
Other font styles liked:
- Playfair Display
Requirements
Must have
- Playfair display font to be consistent with our logo (attached). Logo also included please. Some consistency with colours of logo please.
Nice to have
- I am a doctor, and have no creative genes! But prefer a clean and professional appearance overall. Not too cluttered in overall appearance.
Should not have
- No cheesy pictures of babies.

```html
<!DOCTYPE html>
<html lang="en">
<head>
<meta charset="utf-8">
<title>Little Lantern – Program Brochure</title>
<link rel="stylesheet" href="https://fonts.googleapis.com/css2?family=Playfair+Display:wght@700&family=Arimo:wght@400;700&display=swap">
<style>
:root{
  --green:#6dbf3f;
  --green-dark:#4f9a2b;
  --grey:#6d6e71;
  --grey-mid:#a7a9ac;
  --grey-light:#dcdddf;
  --paper:#f7f8f6;
  --ink:#1e1e1e;
  --label-dark:#2c3a22;
  --white:#ffffff;
}
*{margin:0;padding:0;box-sizing:border-box}
html,body{width:1200px;height:848px;overflow:hidden;background:var(--paper)}
.brochure{position:relative;width:1200px;height:848px;overflow:hidden;
  font-family:"Arimo",Arial,sans-serif;color:var(--ink);font-size:15px;line-height:18.6px;
  background:linear-gradient(180deg,#f0f4ec 0%,#ffffff 60%,#f3f7ef 100%)}
.decor{position:absolute;inset:0}
.week-title{position:absolute;font-family:"Playfair Display",Georgia,serif;font-weight:700;font-size:24px;line-height:1;font-variant-numeric:lining-nums}
.week-title.on-green{color:var(--white)}
.week-title.on-light{color:var(--green)}
.week-title.on-grey{color:var(--white)}
.intro{position:absolute;width:342px}
.doctor{color:var(--green);font-weight:700}
.topics{list-style:none;margin-top:1px}
.topics li{position:relative;padding-left:18px;line-height:23px}
.topics li::before{content:"";position:absolute;left:2px;top:7px;border-left:6px solid var(--green);
  border-top:4.5px solid transparent;border-bottom:4.5px solid transparent}
.session-column{position:absolute;left:426px;width:345px}
.session + .session{margin-top:18px}
.session-label{font-family:"Playfair Display",Georgia,serif;font-weight:700;font-size:15.5px;font-variant-numeric:lining-nums}
.session-green .session-label{color:var(--label-dark)}
.session-grey .session-label{color:var(--green-dark)}
</style>
</head>
<body>
<main class="brochure">
  <svg class="decor" width="1200" height="848" viewBox="0 0 1200 848" aria-hidden="true">
    <defs>
      <linearGradient id="greyPanel" x1="0" y1="0" x2="0" y2="1">
        <stop offset="0" stop-color="#d7d8da"/><stop offset="1" stop-color="#f1f1f1"/>
      </linearGradient>
    </defs>
    <rect x="400" y="0" width="400" height="402" fill="var(--green)"/>
    <rect x="400" y="402" width="400" height="446" fill="url(#greyPanel)"/>
    <polygon points="0,0 30,0 0,40" fill="var(--grey-mid)"/>
    <polygon points="30,0 250,0 250,28 140,96 30,28" fill="var(--green)"/>
    <polygon points="250,0 282,0 262,22" fill="var(--grey)"/>
    <polygon points="290,0 340,0 315,22" fill="var(--grey-light)"/>
    <polygon points="400,0 640,0 640,24 520,94 400,24" fill="#f2f4ef"/>
    <polygon points="400,0 470,0 400,60" fill="var(--grey-light)" opacity=".8"/>
    <polygon points="600,0 650,0 625,22" fill="var(--grey)"/>
    <polygon points="400,402 800,402 800,430 640,430 520,494 400,430" fill="#c4c6c8"/>
    <polygon points="440,402 640,402 640,432 520,496 440,432" fill="var(--grey)"/>
    <polygon points="640,402 800,402 720,470" fill="var(--white)" opacity=".7"/>
    <polygon points="800,0 828,0 800,36" fill="var(--grey-mid)"/>
    <polygon points="828,0 1000,0 1000,28 914,96 828,28" fill="var(--green)"/>
    <polygon points="1000,0 1030,0 1012,22" fill="var(--grey)"/>
    <polygon points="1040,0 1090,0 1065,22" fill="var(--grey-light)"/>
    <polygon points="300,430 370,500 300,570 230,500" fill="var(--grey)" opacity=".85"/>
    <polygon points="0,560 60,620 0,680" fill="var(--green)" opacity=".25"/>
    <polygon points="60,780 130,848 0,848" fill="var(--green)" opacity=".15"/>
    <polygon points="1200,560 1200,760 1110,660" fill="var(--grey)" opacity=".85"/>
    <polygon points="1150,760 1200,710 1200,810" fill="var(--grey-light)"/>
    <polygon points="880,820 910,790 940,820" fill="var(--green)" opacity=".2"/>
  </svg>

  <h2 class="week-title on-green" style="left:56px;top:20px">Week 1</h2>
  <div class="intro" style="left:26px;top:110px">
    <p>GP <span class="doctor">Dr Hannah Whitfield</span> will share information for Mum’s own health after delivery.<br>Topics include:</p>
    <ul class="topics">
      <li>Vaccinations in pregnancy</li>
      <li>Bleeding, bladder and bowel after delivery</li>
      <li>Breastfeeding, engorgement and mastitis</li>
      <li>Bottle feeding</li>
      <li>Post-natal anxiety &amp; depression</li>
      <li>Intimacy and contraception</li>
    </ul>
  </div>
  <svg style="position:absolute;left:0;top:320px" width="400" height="528" viewBox="0 320 400 528" role="img" aria-label="Photographs: gloved hands preparing a vaccination syringe, and a baby's hand held by a parent">
    <defs>
      <linearGradient id="vacc" x1="0" y1="0" x2="1" y2="1"><stop offset="0" stop-color="#e8f1fa"/><stop offset="1" stop-color="#7fb0dc"/></linearGradient>
      <linearGradient id="skin" x1="0" y1="0" x2="1" y2="1"><stop offset="0" stop-color="#f1d7c6"/><stop offset="1" stop-color="#c99a82"/></linearGradient>
    </defs>
    <polygon points="180,340 320,440 210,545 75,445" fill="url(#vacc)"/>
    <polygon points="198,470 376,648 198,826 20,648" fill="var(--white)"/>
    <polygon points="198,484 362,648 198,812 34,648" fill="url(#skin)"/>
  </svg>

  <h2 class="week-title on-light" style="left:456px;top:20px">Week 2</h2>
  <div class="session-column" style="top:108px">
    <p class="session session-green"><span class="session-label">Session 1</span> – Clinical Psychologist Dr Maren Ellsworth will discuss changes in relationships as couples becomes parents, gender roles in parenting and post-natal depression.</p>
    <p class="session session-green"><span class="session-label">Session 2</span> – Physiotherapist Tessa Harlow will present advice for Mums regarding exercise during and after pregnancy, looking after the pelvic floor during and after pregnancy, and abdominal muscle separation management. She will also provide advice for promoting babies’ neck strength and minimising the risk of flat spots on the head and encouraging gross motor skills in the first 6 months.</p>
  </div>

  <h2 class="week-title on-grey" style="left:456px;top:424px">Week 3</h2>
  <div class="session-column" style="top:508px">
    <p class="session session-grey"><span class="session-label">Session 1</span> – Dietician Nadia Brennan provides advice for Mums regarding healthy eating during pregnancy and lactation, normal weight gain during pregnancy and realistic weight loss after. She will also discuss the evidence regarding breastfeeding VS bottle-feeding, normal infant weight gain and introducing solids (including those with potential for allergy).</p>
    <p class="session session-grey"><span class="session-label">Session 2</span> – Paediatric Speech Pathologist Clara Moss will share information about latching and breast-feeding troubles &amp; tongue tie, advice about dummies and finger-sucking, introducing solids &amp; feeding (including ‘pouch’ food), encouraging language development and current evidence about electronic devices impacting language development.</p>
  </div>

  <h2 class="week-title on-green" style="left:856px;top:20px">Week 4</h2>
  <div class="intro" style="left:826px;top:110px">
    <p>GP <span class="doctor">Dr Hannah Whitfield</span> will share advice about your babies’ health in the first 6 months, including:</p>
    <ul class="topics">
      <li>Skin of newborns</li>
      <li>Sleeping</li>
      <li>Crying</li>
      <li>Immunisations</li>
      <li>Fever and infections</li>
      <li>Diarrhoea and constipation</li>
      <li>Teething</li>
      <li>Understanding a baby’s signals</li>
    </ul>
  </div>
  <svg style="position:absolute;left:800px;top:350px" width="400" height="498" viewBox="800 350 400 498" role="img" aria-label="Photographs: a newborn baby, and a mother holding her infant close">
    <defs>
      <linearGradient id="newborn" x1="0" y1="0" x2="1" y2="1"><stop offset="0" stop-color="#f6ece8"/><stop offset="1" stop-color="#d9a99a"/></linearGradient>
      <linearGradient id="mother" x1="0" y1="0" x2="1" y2="1"><stop offset="0" stop-color="#f4ede8"/><stop offset="1" stop-color="#b98672"/></linearGradient>
    </defs>
    <polygon points="1090,358 1220,488 1090,618 960,488" fill="var(--white)"/>
    <polygon points="1090,372 1206,488 1090,604 974,488" fill="url(#newborn)"/>
    <polygon points="978,462 1158,642 978,822 798,642" fill="var(--white)"/>
    <polygon points="978,476 1144,642 978,808 812,642" fill="url(#mother)"/>
  </svg>
</main>
</body>
</html>
```